Website Redesign - We Need Your Magic!

Hello we are looking for you to help us re-design a high end and professional website for a high-end private school.

Here is the current site: http://www.ferndalecrest.com/

NOTE THIS IS DESIGN ONLY, NO CODING :)

The image they want to portray is that of high quality sports and education, in a creative "un-stiff" way.

Menu Bar: Horizontal

Look and Feel:

Site Colors: Dark green and a Gold yellow (logos are attached)

This site will represent a school so the look must be clean, bold, and classy. The site must have a very clean user interface, with things easily recognizable. Think simple.

The site should be visually appealing! If you come to me with templates, or a ton of text you will be out.

This site should be outside the box, we do not want boring, we do not want status quo. This site should instill excitement, innovation, and athletics.

So the main points again are:

1. High-end and classy look, with creative feel
2. Simple and clear navigation style
3. To cover the Junior and High School - Ferndale Crest College Schools

Think outside the box. We look forward to seeing what you come up with!!

Thank you for helping us create an amazing site for the school!

Industry/Entity Type

School

```html
<!DOCTYPE html>
<html lang="en">
<head>
<meta charset="utf-8">
<title>Ferndale Crest College</title>
<link rel="stylesheet" href="https://fonts.googleapis.com/css2?family=Ubuntu:wght@300;400;500&family=Arimo:wght@400&display=swap">
<style>
  :root {
    --green: #0f6b3a;
    --green-dark: #0b5a30;
    --green-line: #1f7a47;
    --gold: #f5e61c;
    --text: #444;
    --text-soft: #666;
    --white: #fff;
    --dot: #c8c8c8;
    --hero-top: #a3b2b9;
    --hero-mid: #dfe5e7;
    --hero-low: #eceeee;
  }
  * { margin: 0; padding: 0; box-sizing: border-box; }
  html, body { width: 927px; height: 1200px; overflow: hidden; background: var(--white); }
  body { font-family: "Ubuntu", sans-serif; color: var(--text); }
  .page { position: relative; width: 927px; height: 1200px; overflow: hidden; }

  .top-strip { position: absolute; top: 0; left: 0; width: 927px; height: 5px; background: var(--green); z-index: 3; }

  .hero {
    position: absolute; top: 0; left: 0; width: 927px; height: 518px;
    background: linear-gradient(180deg, var(--hero-top) 0%, var(--hero-mid) 45%, var(--hero-low) 100%);
  }

  .main-nav {
    position: absolute; top: 5px; left: 378px; width: 449px; height: 36px;
    background: var(--green); display: flex; align-items: center; justify-content: space-around;
    padding: 0 10px; z-index: 4;
  }
  .main-nav a { color: var(--white); text-decoration: none; font-size: 12px; white-space: nowrap; }

  .brand {
    position: absolute; top: 98px; left: 108px; display: flex; align-items: center; gap: 8px; z-index: 4;
  }
  .brand-mark { width: 18px; height: 18px; border-radius: 50%; background: var(--green); flex: none; }
  .brand-name { font-size: 18px; font-weight: 500; color: var(--green); white-space: nowrap; }

  .slider-dots { position: absolute; top: 479px; left: 434px; display: flex; gap: 3px; }
  .slider-dots span { width: 11px; height: 11px; border-radius: 50%; background: var(--dot); }
  .slider-dots span.active { background: var(--green); }

  .welcome-title {
    position: absolute; top: 577px; left: 99px; width: 728px;
    display: flex; align-items: center; gap: 14px;
    font-size: 24px; font-weight: 300; color: var(--green); white-space: nowrap;
  }
  .welcome-title::before, .welcome-title::after { content: ""; flex: 1; height: 2px; background: var(--green); }

  .welcome-quote {
    position: absolute; top: 628px; left: 96px; width: 734px;
    text-align: center; font-size: 14.2px; line-height: 23px; font-weight: 300; color: var(--text);
  }

  .feature { position: absolute; top: 737px; width: 170px; text-align: center; }
  .feature-icon {
    width: 87px; height: 87px; margin: 0 auto; border-radius: 50%; background: var(--green);
    display: flex; align-items: center; justify-content: center;
  }
  .feature-title { margin-top: 13px; font-size: 15px; font-weight: 400; color: var(--green); white-space: nowrap; }
  .feature-text { margin-top: 6px; font-size: 9.6px; line-height: 16px; font-weight: 300; color: var(--text-soft); }

  .site-footer {
    position: absolute; top: 962px; left: 0; width: 927px; height: 238px; background: var(--green); color: var(--white);
  }
  .footer-col { position: absolute; top: 38px; }
  .footer-heading { font-family: "Arimo", sans-serif; font-size: 14px; font-weight: 400; margin-bottom: 12px; }
  .footer-list { list-style: none; font-size: 10px; line-height: 18.5px; }
  .contact-row { display: flex; align-items: flex-start; gap: 10px; font-size: 10px; line-height: 16px; margin-bottom: 6px; }
  .contact-row svg { flex: none; margin-top: 2px; }
  .footer-text { font-size: 9.6px; line-height: 18px; }
  .social { display: flex; gap: 6px; margin-top: 10px; }
  .social span { width: 20px; height: 20px; border-radius: 50%; background: var(--white); }
  .newsletter-input { display: block; width: 174px; height: 22px; margin-top: 9px; background: var(--white); border: none; }
  .subscribe-btn {
    display: block; margin: 12px 0 0 95px; width: 78px; height: 24px; background: var(--gold); color: var(--green-dark);
    font-family: "Ubuntu", sans-serif; font-size: 11px; border: none;
  }
  .footer-rule { position: absolute; top: 184px; left: 99px; width: 728px; height: 1px; background: var(--green-line); }
  .copyright { position: absolute; top: 205px; left: 100px; font-family: "Arimo", sans-serif; font-size: 9.6px; }
</style>
</head>
<body>
<div class="page">
  <div class="hero" role="img" aria-label="Hero photo: a boy throwing a paper plane and kicking a football on a misty road, with an open book and paper planes on the ground"></div>
  <div class="top-strip"></div>

  <nav class="main-nav">
    <a href="#">Home</a>
    <a href="#">About Us</a>
    <a href="#">Academics</a>
    <a href="#">Sports</a>
    <a href="#">Joining Ferndale Crest</a>
    <a href="#">Contact</a>
  </nav>

  <div class="brand">
    <span class="brand-mark"></span>
    <span class="brand-name">Ferndale Crest</span>
  </div>

  <div class="slider-dots"><span class="active"></span><span></span><span></span><span></span></div>

  <h1 class="welcome-title">Welcome to Ferndale Crest College</h1>
  <p class="welcome-quote">“Claritas est etiam processus dynamicus, qui sequitur mutationem consuetudium lectorum. Mirum est notare quam littera gothica quam nunc putamus parum claram, anteposuerit litterarum formas humanitatis per seacula quarta decima et quinta decima. Eodem modo typi, qui nunc nobis videntur parum clari, fiant sollemnes in futurum.”</p>

  <section class="feature" style="left:88px">
    <div class="feature-icon">
      <svg width="44" height="36" viewBox="0 0 44 36"><path d="M2 17 L42 2 L30 34 L22 22 Z" fill="var(--gold)"/><path d="M22 22 L42 2 L14 19 Z" fill="var(--green-dark)"/></svg>
    </div>
    <h2 class="feature-title">Photo Gallery</h2>
    <p class="feature-text">Claritas est eteus dynamicuin<br>qui sequitur mutatiem consuetlaritas<br>dynamicusClaritas est etiam.</p>
  </section>

  <section class="feature" style="left:288px">
    <div class="feature-icon">
      <svg width="36" height="36" viewBox="0 0 36 36" fill="none" stroke="var(--gold)" stroke-width="2.5"><rect x="3" y="6" width="30" height="27" rx="2"/><line x1="11" y1="2" x2="11" y2="9"/><line x1="25" y1="2" x2="25" y2="9"/><g fill="var(--gold)" stroke="none"><rect x="8" y="14" width="4" height="4"/><rect x="16" y="14" width="4" height="4"/><rect x="24" y="14" width="4" height="4"/><rect x="8" y="21" width="4" height="4"/><rect x="16" y="21" width="4" height="4"/><rect x="24" y="21" width="4" height="4"/></g></svg>
    </div>
    <h2 class="feature-title">School Calender</h2>
    <p class="feature-text">Claritas est eteus dynamicuin<br>qui sequitur mutatiem consuetlaritas<br>dynamicusClaritas est etiam.</p>
  </section>

  <section class="feature" style="left:480px">
    <div class="feature-icon">
      <svg width="44" height="44" viewBox="0 0 44 44"><g fill="var(--gold)"><rect x="18" y="2" width="8" height="40" rx="1"/><rect x="18" y="2" width="8" height="40" rx="1" transform="rotate(45 22 22)"/><rect x="18" y="2" width="8" height="40" rx="1" transform="rotate(90 22 22)"/><rect x="18" y="2" width="8" height="40" rx="1" transform="rotate(135 22 22)"/><circle cx="22" cy="22" r="14"/></g><circle cx="22" cy="22" r="6" fill="var(--green)"/></svg>
    </div>
    <h2 class="feature-title">Special Events</h2>
    <p class="feature-text">Claritas est eteus dynamicuin<br>qui sequitur mutatiem consuetlaritas<br>dynamicusClaritas est etiam.</p>
  </section>

  <section class="feature" style="left:669px">
    <div class="feature-icon">
      <svg width="48" height="40" viewBox="0 0 48 40"><path d="M4 15 H12 L30 5 V33 L12 23 H4 Z" fill="var(--gold)"/><path d="M12 23 L16 36 H21 L18 24 Z" fill="var(--gold)"/><g fill="none" stroke="var(--gold)" stroke-width="2.5" stroke-linecap="round"><path d="M35 13 Q39 19 35 25"/><path d="M40 9 Q46 19 40 29"/></g></svg>
    </div>
    <h2 class="feature-title">Sports Announcements</h2>
    <p class="feature-text">Claritas est eteus dynamicuin<br>qui sequitur mutatiem consuetlaritas<br>dynamicusClaritas est etiam.</p>
  </section>

  <footer class="site-footer">
    <div class="footer-col" style="left:100px">
      <h3 class="footer-heading">Downloads</h3>
      <ul class="footer-list">
        <li>Duis autem vel</li>
        <li>Eodem modo typi</li>
        <li>validations and verification</li>
        <li>System monitoring</li>
        <li>Emergency Breakdowns</li>
      </ul>
    </div>

    <div class="footer-col" style="left:285px">
      <h3 class="footer-heading">Contact Us</h3>
      <div class="contact-row">
        <svg width="9" height="12" viewBox="0 0 9 12"><path d="M4.5 0 A4.5 4.5 0 0 1 9 4.5 C9 7.5 4.5 12 4.5 12 C4.5 12 0 7.5 0 4.5 A4.5 4.5 0 0 1 4.5 0 Z" fill="#cfe3d6"/><circle cx="4.5" cy="4.5" r="1.6" fill="var(--green)"/></svg>
        <span>240 Willowmere Rd.<br>Ashford Vale 40517</span>
      </div>
      <div class="contact-row">
        <svg width="12" height="9" viewBox="0 0 12 9"><rect width="12" height="9" fill="#cfe3d6"/><path d="M0 0 L6 5 L12 0" fill="none" stroke="var(--green)" stroke-width="1"/></svg>
        <span>hello@ferndalecrest.edu</span>
      </div>
      <div class="contact-row">
        <svg width="11" height="11" viewBox="0 0 11 11"><path d="M2 0 L4 3 L3 4.5 Q4.5 6.5 6.5 8 L8 7 L11 9 L9.5 11 Q4 10 0 2 Z" fill="#cfe3d6"/></svg>
        <span>55 014 2287</span>
      </div>
    </div>

    <div class="footer-col" style="left:464px">
      <h3 class="footer-heading">Follow Us</h3>
      <p class="footer-text">Follow us our news and events<br>through social networks.</p>
      <div class="social"><span></span><span></span><span></span><span></span></div>
    </div>

    <div class="footer-col" style="left:649px">
      <h3 class="footer-heading">Newsletter</h3>
      <p class="footer-text">Stay in touch with us by signing up for our<br>quarterly newsletter!</p>
      <input class="newsletter-input" type="email" aria-label="Email address">
      <button class="subscribe-btn" type="button">SUBSCRIBE</button>
    </div>

    <div class="footer-rule"></div>
    <p class="copyright">Copyright ©2013. All Rights Reserved.</p>
  </footer>
</div>
</body>
</html>
```